Lawn Sign Design – Brisqel

We need a clean, eye-catching 18" x 24" lawn sign for Brisqel that effectively communicates our core message while maintaining strong brand consistency.

Key Elements to Include:
Tagline (Main Focus): Upgrade Your Roof Without Replacing It
Website: www.trybrisqel.com
Phone Number: (888) BRISQEL-GO
TWQB License Number: 4480512
Brisqel Logo & Branding: Ensure the logo, corporate colors, and custom font are used consistently to align with our existing branding.

Design Guidelines:
Simple & High-Impact: The tagline should be the most prominent element on the sign, drawing immediate attention.
Easy Readability: Use a bold, clean design with high contrast for quick readability from a distance.
Balanced Layout: Place supporting details (website, phone number, and TWQB number) in a visually clear but secondary position to the tagline.
Professional & Modern: The sign should reflect credibility and innovation in the roofing industry.

Deliverables:
High-resolution print-ready files (CMYK)
A digital proof for review before finalizing
The final design should make a strong impression with minimal text, ensuring that anyone passing by can instantly grasp what we offer.

I am including our custom font. To get an hexagon in our name, simply type the $ after the 'O" Please use this font for anything you type.

```html
<!DOCTYPE html>
<html lang="en">
<head>
<meta charset="utf-8">
<title>Brisqel Lawn Sign</title>
<link rel="stylesheet" href="https://fonts.googleapis.com/css2?family=Nunito:wght@700;800;900&display=swap">
<style>
  :root {
    --backdrop: #3c3f42;
    --paper: #ffffff;
    --brand-blue: #245796;
    --brand-cyan: #0277b5;
    --ink: #000000;
    --on-blue: #ffffff;
  }
  * { margin: 0; padding: 0; box-sizing: border-box; }
  html, body {
    width: 944px;
    height: 1200px;
    overflow: hidden;
    background: var(--backdrop);
    font-family: "Nunito", sans-serif;
  }
  .lawn-sign {
    position: absolute;
    left: 102px;
    top: 106px;
    width: 740px;
    height: 987px;
    background: var(--paper);
    overflow: hidden;
  }
  .brand-name {
    position: absolute;
    left: 30px;
    top: 64px;
    font-size: 118px;
    font-weight: 900;
    line-height: 1;
    letter-spacing: 2px;
    color: var(--brand-blue);
  }
  .accent-band {
    position: absolute;
    left: 0;
    top: 0;
    width: 740px;
    height: 987px;
  }
  .tagline {
    position: absolute;
    left: 58px;
    top: 385px;
    color: var(--brand-blue);
    font-weight: 900;
    font-size: 92px;
    line-height: 104px;
    letter-spacing: 1px;
  }
  .tagline-sub {
    position: absolute;
    left: 58px;
    top: 587px;
    color: var(--ink);
    font-weight: 900;
    font-size: 50px;
    line-height: 1;
    letter-spacing: 0.5px;
    white-space: nowrap;
  }
  .phone-bar {
    position: absolute;
    left: 55px;
    top: 691px;
    width: 631px;
    height: 102px;
    border-radius: 10px;
    background: var(--ink);
    overflow: hidden;
  }
  .phone-icon {
    position: absolute;
    left: 26px;
    top: 27px;
    width: 48px;
    height: 48px;
  }
  .phone-number {
    position: absolute;
    left: 98px;
    top: 0;
    right: 0;
    bottom: 0;
    border-radius: 10px;
    background: linear-gradient(90deg, var(--brand-cyan) 0%, var(--brand-blue) 22%, var(--brand-cyan) 62%, var(--brand-blue) 100%);
    color: var(--on-blue);
    font-weight: 900;
    font-size: 50px;
    display: flex;
    align-items: center;
    justify-content: center;
    letter-spacing: 1px;
    white-space: nowrap;
  }
  .website {
    position: absolute;
    left: 76px;
    top: 850px;
    display: flex;
    align-items: center;
    gap: 20px;
  }
  .globe-icon { width: 58px; height: 58px; }
  .website-url {
    font-weight: 900;
    font-size: 50px;
    line-height: 1;
    color: var(--ink);
    white-space: nowrap;
  }
  .license {
    position: absolute;
    left: 0;
    right: 0;
    top: 928px;
    text-align: center;
    color: var(--brand-blue);
    font-weight: 800;
    font-size: 26px;
    line-height: 1;
  }
</style>
</head>
<body>
  <main class="lawn-sign">
    <div class="brand-name">BRISQEL</div>

    <svg class="accent-band" viewBox="0 0 740 987" aria-hidden="true">
      <defs>
        <linearGradient id="band-gradient" x1="0" y1="0" x2="740" y2="0" gradientUnits="userSpaceOnUse">
          <stop offset="0" stop-color="#0277b5"/>
          <stop offset="0.18" stop-color="#245796"/>
          <stop offset="0.7" stop-color="#0277b5"/>
          <stop offset="1" stop-color="#245796"/>
        </linearGradient>
      </defs>
      <polyline points="-20,319 542,319 651,409 760,309"
        fill="none" stroke="url(#band-gradient)" stroke-width="34"
        stroke-linejoin="round" stroke-linecap="butt"/>
    </svg>

    <h1 class="tagline">UPGRADE<br>YOUR ROOF</h1>
    <p class="tagline-sub">WITHOUT REPLACING IT</p>

    <div class="phone-bar">
      <svg class="phone-icon" viewBox="0 0 48 48" aria-hidden="true">
        <path d="M4 4h11v13h-5c0 12 9 21 21 21v-5h13v11H31C15 44 4 33 4 17z" fill="#ffffff"/>
      </svg>
      <div class="phone-number">(888) BRISQEL-GO</div>
    </div>

    <div class="website">
      <svg class="globe-icon" viewBox="0 0 58 58" aria-hidden="true">
        <circle cx="29" cy="29" r="27" fill="#245796"/>
        <ellipse cx="29" cy="29" rx="11" ry="27" fill="none" stroke="#ffffff" stroke-width="3"/>
        <line x1="2" y1="29" x2="56" y2="29" stroke="#ffffff" stroke-width="3"/>
        <path d="M7 16h44M7 42h44" stroke="#ffffff" stroke-width="3" fill="none"/>
      </svg>
      <span class="website-url">www.trybrisqel.com</span>
    </div>

    <p class="license">TWQB License Number: 4480512</p>
  </main>
</body>
</html>
```